brovlanepass.net

Develop a website for brolanepass.net will be a site to sell tickets for concerts, shows, shows, theaters and others. I need a web design easy view, very easy to use and accumulate events by date. The aim is to develop the site was connected to a complex system that is already developed. (Important this page to a robust system was connected via links the idea is to develop only the front view)
Updates

Reason: I need more designs yet we have not made the decision

Target Market(s)

millennials, adults, who want to enjoy concerts and shows

Industry/Entity Type

Event

Number of Pages Required

5+ page

Colors
1b1b1b
aaaaaa
ffffff

Requirements
Must have
• Easy Vista, accumulation of upcoming events, past events. The tabs should have are: 1 Start: In this part of upcoming events occur. You could put a banner on the top and down the events by date. 2. How to order: page with instructions on how to purchase tickets 3. About Us: The company history 4. Contact: Phones and template for contact by mail 5. Our policies: shopping 6. Notice Privacy: Privacy Notice Copoy 7. Centers Sale: physical places where they can purchase tickets Promoters 8. access: Link to a template
Nice to have
• as you can see p www.quimbarostage.net or farunda.net or farunda.org or gallowmerk.net (important this page to a robust system was connected via links the idea is to develop only the front view)
Should not have
• Many things Tangled

```html
<!DOCTYPE html>
<html lang="en">
<head>
<meta charset="utf-8">
<title>Brovlanepass</title>
<link href="https://fonts.googleapis.com/css2?family=Open+Sans:wght@400;600;700;800&display=swap" rel="stylesheet">
<style>
:root{
  --ink:#ffffff;
  --muted:#cfc7cb;
  --accent:#e5484d;
  --nav:#141214;
  --nav-active:#0b0a0b;
  --header:#1c0b12;
  --page:#1d0b13;
  --footer:#141012;
  --line:#3a3236;
  --band:rgba(20,14,18,.82);
}
*{box-sizing:border-box;margin:0;padding:0}
html,body{width:783px;height:1200px;overflow:hidden;background:var(--page)}
body{font-family:"Open Sans",sans-serif;color:var(--ink);position:relative}
.abs{position:absolute}

.site-header{left:0;top:0;width:783px;height:73px;background:radial-gradient(ellipse at 60% 40%,#2a0f1b,var(--header))}
.phone{left:68px;top:22px;display:flex;align-items:center;gap:8px;font-size:14px}
.phone-icon{width:28px;height:28px;border:1.5px solid var(--ink);border-radius:50%;display:flex;align-items:center;justify-content:center}
.brand{display:flex;align-items:center;gap:6px;font-weight:800;letter-spacing:.5px;color:var(--ink)}
.brand-mark{background:var(--accent);border-radius:2px}
.brand.top{left:320px;top:26px;font-size:15px}
.brand.top .brand-mark{width:18px;height:18px}
.social{display:flex;gap:8px}
.social span{display:block;width:15px;height:15px;border-radius:3px}
.social.top{left:628px;top:28px}
.social.top span:nth-child(1){background:#2d6fc4}
.social.top span:nth-child(2){background:#2ba6e4}
.social.top span:nth-child(3){background:#2877b5}
.social.top span:nth-child(4){background:#d3463a}

.main-nav{left:0;top:73px;width:783px;height:38px;background:var(--nav);display:flex;padding-left:58px;font-size:11px}
.main-nav a{color:var(--ink);text-decoration:none;display:flex;align-items:center;padding:0 16px;height:38px}
.main-nav a.active{background:var(--nav-active);border-top:2px solid var(--accent);padding:0 21px}

.hero{left:0;top:111px;width:783px;height:321px;background:
  radial-gradient(ellipse at 45% 10%,#c9d3f3 0%,#6f7fc8 25%,transparent 55%),
  radial-gradient(ellipse at 80% 60%,#5a4a8c 0%,transparent 60%),
  linear-gradient(180deg,#3d3f7d 0%,#2a2350 50%,#120c1c 100%)}
.hero-title{left:62px;top:256px;font-size:38px;font-weight:800;letter-spacing:-.5px;line-height:1}
.hero-sub{left:63px;top:306px;font-size:21px;font-weight:400}
.hero-arrows{left:686px;top:396px;display:flex;gap:4px}
.hero-arrows span{width:18px;height:18px;border-radius:50%;background:rgba(0,0,0,.55);display:flex;align-items:center;justify-content:center}

.section-title{left:0;top:468px;width:783px;text-align:center;font-size:19px;font-weight:600;letter-spacing:.3px}

.event{width:217px;height:203px;overflow:hidden}
.event-photo{position:absolute;inset:0}
.event-band{position:absolute;left:0;bottom:0;width:100%;height:47px;background:var(--band)}
.event-date{position:absolute;left:0;bottom:0;width:35px;height:47px;background:var(--accent);font-size:8px;text-align:center;line-height:12px;padding-top:6px}
.event-name{position:absolute;left:42px;bottom:22px;font-size:10.5px;font-weight:600;border-bottom:1px solid var(--muted);padding-bottom:1px}
.event-desc{position:absolute;left:42px;bottom:9px;font-size:7.5px;color:var(--muted)}
.book-btn{position:absolute;right:9px;bottom:17px;border:1px solid var(--ink);border-radius:8px;font-size:6.5px;padding:2px 8px}

.view-more{left:344px;top:962px;width:95px;height:24px;border:1px solid var(--ink);border-radius:12px;font-size:11px;display:flex;align-items:center;justify-content:center}

.site-footer{left:0;top:1010px;width:783px;height:190px;background:var(--footer)}
.brand.foot{left:58px;top:1081px;font-size:13px}
.brand.foot .brand-mark{width:16px;height:16px}
.foot-h{font-size:10px;top:1048px}
.contact-list{left:224px;top:1075px;font-size:8px;line-height:14.5px}
.mail-copy{left:419px;top:1072px;font-size:7px;line-height:11px;width:135px}
.mail-form{left:419px;top:1099px;display:flex}
.mail-form .field{width:95px;height:20px;background:#fff;color:#999;font-size:7px;padding:6px 5px}
.mail-form .submit{width:37px;height:20px;background:#55504f;font-size:7px;display:flex;align-items:center;justify-content:center}
.social.foot{left:615px;top:1079px;gap:10px}
.social.foot span{width:16px;height:16px;background:var(--ink)}
.foot-rule{left:50px;top:1156px;width:667px;height:1px;background:var(--line)}
.copyright{left:0;top:1173px;width:783px;text-align:center;font-size:8px}
</style>
</head>
<body>

<header class="site-header abs"></header>
<div class="phone abs">
  <span class="phone-icon"><svg width="12" height="12" viewBox="0 0 24 24"><path fill="#fff" d="M6.6 10.8a15 15 0 0 0 6.6 6.6l2.2-2.2c.3-.3.7-.4 1-.2 1.1.4 2.3.6 3.6.6.6 0 1 .4 1 1V20c0 .6-.4 1-1 1A17 17 0 0 1 3 4c0-.6.4-1 1-1h3.5c.6 0 1 .4 1 1 0 1.3.2 2.5.6 3.6.1.3 0 .7-.2 1z"/></svg></span>
  +852 5550 1982
</div>
<div class="brand top abs"><span class="brand-mark"></span>BROVLANEPASS</div>
<div class="social top abs"><span></span><span></span><span></span><span></span></div>

<nav class="main-nav abs">
  <a class="active">HOME</a><a>HOW TO ORDER</a><a>ABOUT US</a><a>CONTACT US</a><a>POLICIES</a><a>PRIVACY</a><a>CENTER SALE</a><a>ACCESS</a>
</nav>

<section class="hero abs" role="img" aria-label="Concert crowd with raised hands under blue stage lights"></section>
<h1 class="hero-title abs">BROVLANEPASS</h1>
<p class="hero-sub abs">quisquam est qui dolorem ipsum</p>
<div class="hero-arrows abs">
  <span><svg width="8" height="8" viewBox="0 0 10 10"><path d="M6.5 1.5 3 5l3.5 3.5" stroke="#fff" stroke-width="1.5" fill="none"/></svg></span>
  <span><svg width="8" height="8" viewBox="0 0 10 10"><path d="M3.5 1.5 7 5 3.5 8.5" stroke="#fff" stroke-width="1.5" fill="none"/></svg></span>
</div>

<h2 class="section-title abs">UPCOMING EVENTS</h2>

<article class="event abs" style="left:58px;top:513px">
  <div class="event-photo" role="img" aria-label="Rock band performing on a lit stage" style="background:linear-gradient(160deg,#4a3c66,#241b2c 50%,#3b4a6a)"></div>
  <div class="event-band"></div><div class="event-date">1<br>NOV<br>2017</div>
  <div class="event-name">NEQUE PORRO</div><div class="event-desc">Dolorem ipsum quia dolor</div><div class="book-btn">BOOK NOW</div>
</article>
<article class="event abs" style="left:283px;top:513px">
  <div class="event-photo" role="img" aria-label="Crowd facing warm orange stage lights" style="background:radial-gradient(ellipse at 50% 20%,#f0a24a,#8a3a14 45%,#1e0f0a 90%)"></div>
  <div class="event-band"></div><div class="event-date">2<br>NOV<br>2017</div>
  <div class="event-name">NEQUE PORRO</div><div class="event-desc">Dolorem ipsum quia dolor</div><div class="book-btn">BOOK NOW</div>
</article>
<article class="event abs" style="left:509px;top:513px">
  <div class="event-photo" role="img" aria-label="Guitarist at a microphone in pink light" style="background:linear-gradient(135deg,#8a4a6e,#3a1c30 55%,#5a2a48)"></div>
  <div class="event-band"></div><div class="event-date">2<br>NOV<br>2017</div>
  <div class="event-name">NEQUE PORRO</div><div class="event-desc">Dolorem ipsum quia dolor</div><div class="book-btn">BOOK NOW</div>
</article>
<article class="event abs" style="left:58px;top:728px">
  <div class="event-photo" role="img" aria-label="Theatre stage with red curtain and rows of seats" style="background:linear-gradient(120deg,#8a1e2c 0%,#3a3f8a 40%,#c8cde0 65%,#7a2a40)"></div>
  <div class="event-band"></div><div class="event-date">4<br>NOV<br>2017</div>
  <div class="event-name">NEQUE PORRO</div><div class="event-desc">Dolorem ipsum quia dolor</div><div class="book-btn">BOOK NOW</div>
</article>
<article class="event abs" style="left:283px;top:728px">
  <div class="event-photo" role="img" aria-label="Costumed jester juggling clubs" style="background:linear-gradient(160deg,#3a2c3e,#6a3c8a 45%,#b23c6a 70%,#2a1a2a)"></div>
  <div class="event-band"></div><div class="event-date">5<br>NOV<br>2017</div>
  <div class="event-name">NEQUE PORRO</div><div class="event-desc">Dolorem ipsum quia dolor</div><div class="book-btn">BOOK NOW</div>
</article>
<article class="event abs" style="left:509px;top:728px">
  <div class="event-photo" role="img" aria-label="Two guitarists playing in blue smoke" style="background:radial-gradient(ellipse at 70% 30%,#6aa0c8,#1e3a52 50%,#0e1a24)"></div>
  <div class="event-band"></div><div class="event-date">6<br>NOV<br>2017</div>
  <div class="event-name">NEQUE PORRO</div><div class="event-desc">Dolorem ipsum quia dolor</div><div class="book-btn">BOOK NOW</div>
</article>

<div class="view-more abs">VIEW MORE</div>

<footer class="site-footer abs"></footer>
<div class="brand foot abs"><span class="brand-mark"></span>BROVLANEPASS</div>
<h3 class="foot-h abs" style="left:224px;font-weight:400">CONTACT US</h3>
<div class="contact-list abs">
  Address : 2170 Velmora Ave,<br>Castrell, Fl, 33190<br>Phone : 555-014-2290<br>Email : hello@brovlanepass.net
</div>
<h3 class="foot-h abs" style="left:419px;font-weight:400">JOIN OUR MAILING LIST</h3>
<p class="mail-copy abs">Your about us information would fit here nicely.</p>
<div class="mail-form abs"><div class="field">Email address</div><div class="submit">Submit</div></div>
<h3 class="foot-h abs" style="left:614px;font-weight:400">FOLLOW US OUT THERE</h3>
<div class="social foot abs"><span></span><span></span><span></span><span></span></div>
<div class="foot-rule abs"></div>
<p class="copyright abs">Copyright © 2017. All Rights Reserved</p>

</body>
</html>
```